Quendle Pools & Patio Homepage Design

I am looking for someone to design a one-page website for a company called Quendle Pools & Patio. While the content will be different, the design should be similar to https://quendle-example.com/pools-patio/.
Industry/Entity Type
Pool Cleaning Service
Number of Pages Required
1 page
Font styles to use
Other font styles liked:
- See brand guidelines

Requirements
Must have
- Must be similar in style https://quendle-example.com/pools-patio/. Look at the Word Doc for the content.

```html
<!DOCTYPE html>
<html lang="en">
<head>
<meta charset="utf-8">
<title>Quendle Pools &amp; Patio</title>
<link href="https://fonts.googleapis.com/css2?family=Montserrat:wght@600;700;800&family=Open+Sans:wght@400;600;700&display=swap" rel="stylesheet">
<style>
:root{
  --blue:#1c86d8;
  --blue-dark:#0f5fa8;
  --navy:#0b3a66;
  --green:#7cc521;
  --green-dark:#5f9c12;
  --ink:#1d1d1f;
  --muted:#4a4f57;
  --pale:#e6f2fb;
  --black:#0c0c0c;
  --white:#ffffff;
}
*{box-sizing:border-box;margin:0;padding:0}
html,body{width:1200px;height:3896px;overflow:hidden}
body{font-family:"Open Sans",Arial,sans-serif;color:var(--ink);background:var(--white);position:relative}
h1,h2,h3,.logo,.btn{font-family:"Montserrat",Arial,sans-serif}
.btn{display:inline-flex;align-items:center;gap:12px;background:var(--green);color:var(--white);font-weight:700;font-size:15px;padding:12px 20px;border-radius:3px;text-decoration:none}
.btn .arrow{width:22px;height:22px;border-radius:50%;background:var(--white);color:var(--green-dark);display:inline-flex;align-items:center;justify-content:center;font-size:12px}
.accent{color:var(--green)}
.accent-blue{color:var(--blue)}

/* top bar */
.topbar{position:absolute;top:0;left:0;width:1200px;height:32px;background:var(--blue);color:var(--white);font-size:13px;display:flex;justify-content:flex-end;align-items:center;gap:34px;padding-right:40px}
.topbar .pill{background:var(--green);padding:0 14px;height:32px;display:flex;align-items:center}

/* nav */
.nav{position:absolute;top:32px;left:0;width:1200px;height:88px;background:var(--white);display:flex;align-items:center;padding:0 100px 0 120px}
.logo{display:flex;align-items:center;gap:10px;font-weight:800;font-size:40px;color:var(--blue)}
.logo .mark{width:30px;height:30px;border:4px solid var(--green);border-radius:4px}
.menu{margin-left:auto;display:flex;gap:36px;align-items:center;font-size:16px}
.menu a{color:var(--ink);text-decoration:none}
.menu a.active{color:var(--blue);border-bottom:2px solid var(--blue);padding-bottom:4px}

/* hero */
.hero{position:absolute;top:120px;left:0;width:1200px;height:580px;background:linear-gradient(180deg,#5fa8d8 0%,#2f8ccc 45%,#1677c0 100%)}
.hero .photo{position:absolute;inset:0;background:linear-gradient(160deg,#86c3e6 0%,#3b9bd6 40%,#0f6fb8 100%)}
.hero-copy{position:absolute;left:108px;top:160px;width:620px;color:var(--white)}
.hero-copy h1{font-size:37px;line-height:1.3;font-weight:700}
.hero-copy .btn{margin-top:40px;font-size:14px}
.dots{position:absolute;left:460px;top:420px;color:var(--white);font-size:12px;letter-spacing:4px}
.reach{position:absolute;top:120px;right:0;width:416px;height:520px;background:var(--blue);color:var(--white);padding:30px 40px}
.reach h2{font-size:38px;font-weight:700}
.reach .call{font-size:14px;letter-spacing:2px;font-weight:600}
.reach .phone{font-family:"Montserrat",Arial,sans-serif;font-size:52px;font-weight:800;line-height:1.1;margin-bottom:20px}
.field{height:40px;background:var(--navy);border:1px solid #2f74b5;margin-bottom:12px;font-size:13px;padding:11px 14px;color:#cfe3f5}
.radios{font-size:13px;margin-top:4px}
.radios .opts{display:flex;gap:22px;margin-top:8px}
.radios .opts span::before{content:"";display:inline-block;width:10px;height:10px;border-radius:50%;border:2px solid var(--white);margin-right:6px;vertical-align:-1px}
.reach .btn{margin-top:26px;font-size:14px;padding:10px 18px}

/* hexagons */
.hex{clip-path:polygon(25% 3%,75% 3%,100% 50%,75% 97%,25% 97%,0 50%)}
.hex-frame{position:absolute;background:var(--green)}
.hex-inner{position:absolute;inset:14px}

/* about */
.about{position:absolute;top:700px;left:0;width:1200px;height:672px}
.about .hex-frame{left:140px;top:100px;width:410px;height:390px}
.about .hex-inner{background:linear-gradient(150deg,#b7d7ea 0%,#6aa6c9 45%,#2f7fb5 100%)}
.about-copy{position:absolute;left:620px;top:88px;width:520px;font-size:13.5px;line-height:1.6;color:var(--muted)}
.about-copy h2{font-size:40px;color:var(--ink);margin-bottom:16px}
.about-copy p{margin-bottom:16px}

/* services */
.services{position:absolute;top:1372px;left:0;width:1200px;height:468px;background:var(--blue);color:var(--white)}
.services h2{text-align:center;font-size:40px;margin-top:70px}
.cards{position:absolute;top:160px;left:112px;display:flex;gap:24px}
.card{width:310px;height:308px;position:relative;border-radius:4px;overflow:hidden}
.card .img{position:absolute;inset:0}
.card .label{position:absolute;left:0;right:0;bottom:0;padding:20px 32px;background:linear-gradient(0deg,rgba(0,0,0,.75),rgba(0,0,0,0));font-family:"Montserrat",Arial,sans-serif;font-weight:700;font-size:18px}
.c1{background:linear-gradient(160deg,#b9c9a6,#5c7a8a 60%,#2a4a6a)}
.c2{background:linear-gradient(160deg,#3fa6dc,#1478c0 60%,#0b4e8a)}
.c3{background:linear-gradient(160deg,#e8dbc2,#b09a7a 60%,#5c5046)}

/* technician */
.tech{position:absolute;top:1840px;left:0;width:1200px;height:560px;background:var(--pale)}
.tech-copy{position:absolute;left:168px;top:200px;width:420px;text-align:right}
.tech-copy h2{font-size:40px;margin-bottom:14px}
.tech-copy p{font-size:14px;line-height:1.6;color:var(--muted);margin-left:90px}
.tech-copy .btn{margin-top:20px;font-size:14px}
.tech .hex-frame{left:660px;top:140px;width:330px;height:320px}
.tech .hex-inner{background:linear-gradient(160deg,#dfe7ee,#a9b9c8 60%,#6f8090)}

/* service area */
.area{position:absolute;top:2400px;left:0;width:1200px;height:512px}
.area h2{position:absolute;left:478px;top:50px;font-size:40px}
.area .map-box{position:absolute;left:150px;top:130px;width:320px;height:300px;border:5px solid var(--green);padding:14px}
.area .map{width:100%;height:100%;background:linear-gradient(160deg,#d8ecf7,#a9d2ec)}
.area .intro{position:absolute;left:604px;top:150px;font-size:20px;font-weight:700}
.cities{position:absolute;left:506px;top:200px;list-style:none;font-size:18px}
.cities li{height:44px;display:flex;align-items:center;padding-left:100px;width:300px}
.cities li.current{background:var(--green);clip-path:polygon(6% 0,100% 0,100% 100%,6% 100%,0 50%);font-weight:600;justify-content:space-between;padding-right:16px}

/* contact */
.touch{position:absolute;top:2912px;left:0;width:588px;height:608px;background:var(--blue);color:var(--white);padding:60px 100px 0 110px}
.touch h2{font-size:40px;margin-bottom:30px}
.touch .field{margin-bottom:14px;height:44px}
.contact{position:absolute;top:2912px;left:588px;width:612px;height:608px;padding:60px 60px 0 50px}
.contact h2{font-size:40px;margin-bottom:28px}
.contact p{font-size:15px;line-height:1.65;color:var(--muted);width:470px}
.contact .give{margin-top:38px;font-size:26px;color:var(--ink)}

/* footer */
.footer{position:absolute;top:3520px;left:0;width:1200px;height:376px;background:var(--black);color:var(--white)}
.footer .logo{position:absolute;left:130px;top:160px;font-size:40px}
.social{position:absolute;left:136px;top:240px;display:flex;gap:12px}
.social span{width:30px;height:30px;border-radius:50%;border:2px solid #6a6a6a}
.fcol{position:absolute;top:36px;height:310px;border-left:1px solid #2f2f2f;padding-left:36px}
.fcol h3{font-size:17px;margin-bottom:36px}
.fcol h3::before{content:"";display:inline-block;width:4px;height:20px;background:var(--green);margin-right:10px;vertical-align:-4px}
.fcol ul{list-style:none;font-size:13px;line-height:2}
.contact-item{display:flex;gap:14px;margin-bottom:20px;font-size:13px;line-height:1.5}
.contact-item svg{flex:none;margin-top:2px}
.contact-item small{display:block;color:#9a9a9a;font-size:12px}
.copyright{position:absolute;left:0;right:0;bottom:22px;text-align:center;font-size:13px;color:#bdbdbd}
.to-top{position:absolute;right:28px;bottom:36px;width:36px;height:36px;border-radius:4px;background:var(--green);display:flex;align-items:center;justify-content:center}
</style>
</head>
<body>

<div class="topbar">
  <span>Email : info@quendle-example.com</span>
  <span class="pill">Call or Text : 972-555-0143</span>
</div>

<header class="nav">
  <div class="logo"><span class="mark"></span>quendle</div>
  <nav class="menu">
    <a class="active" href="#">Home</a>
    <a href="#">About</a>
    <a href="#">Services</a>
    <a href="#">Blog</a>
    <a href="#">Testimonials</a>
    <a class="btn" href="#" style="color:#fff;padding:10px 18px">Contact Us</a>
  </nav>
</header>

<section class="hero">
  <div class="photo" role="img" aria-label="Photo of a bright blue backyard swimming pool with patio"></div>
  <div class="hero-copy">
    <h1>Professional Pool Cleaning &amp; Repair in the DFW Metroplex | Quendle Pools &amp; Patio</h1>
    <a class="btn" href="#">Contact Us <span class="arrow">➜</span></a>
  </div>
  <div class="dots">● ○ ○</div>
</section>

<aside class="reach">
  <h2>Reach Us</h2>
  <div class="call">OR CALL US</div>
  <div class="phone">972-555-0143</div>
  <div class="field">Your Name</div>
  <div class="field">Email</div>
  <div class="field">Phone Number</div>
  <div class="radios">Preferred Contact Method
    <div class="opts"><span>Call</span><span>Text</span><span>Email</span></div>
  </div>
  <a class="btn" href="#">Submit <span class="arrow">➜</span></a>
</aside>

<section class="about">
  <div class="hex-frame hex"><div class="hex-inner hex" role="img" aria-label="Photo of a technician cleaning a pool beside a patio"></div></div>
  <div class="about-copy">
    <h2>About <span class="accent-blue">Us</span></h2>
    <p>We're Quendle Pools &amp; Patio, and we specialize in pool cleaning and repair services that will keep your pool looking its best. Our reliable and professional team is committed to helping you get the most out of your backyard oasis, ensuring it's always ready for all types of fun when you want it. Our weekly pool cleaning service is affordable and ensures that your pool is properly taken care of throughout the swimming season.</p>
    <p>When you choose us as your go-to for all things pools, relaxing days spent on a clean lounge chair are worry-free because we take care of all the hard work! From chemical balancing to scrubbing and filter maintenance – there's nothing too big or small for us. So don't wait any longer – trust Quendle to keep your pool sparkling all summer!</p>
    <a class="btn" href="#">Book Now <span class="arrow">➜</span></a>
  </div>
</section>

<section class="services">
  <h2>Our Services</h2>
  <div class="cards">
    <div class="card"><div class="img c1" role="img" aria-label="Photo of a technician with pool cleaning equipment"></div><div class="label">Pool Cleaning</div></div>
    <div class="card"><div class="img c2" role="img" aria-label="Photo of pool maintenance in clear blue water"></div><div class="label">Pool Maintenance</div></div>
    <div class="card"><div class="img c3" role="img" aria-label="Photo of a pool equipment repair"></div><div class="label">Pool Repair</div></div>
  </div>
</section>

<section class="tech">
  <div class="tech-copy">
    <h2>Meet Your <span class="accent-blue">Technician</span></h2>
    <p>I understand that keeping your pool clean and well-maintained is a priority for you, which is why I'm committed to providing top-notch pool cleaning and repair services.</p>
    <a class="btn" href="#">Book Now <span class="arrow">➜</span></a>
  </div>
  <div class="hex-frame hex"><div class="hex-inner hex" role="img" aria-label="Portrait photo of the pool technician"></div></div>
</section>

<section class="area">
  <h2>Service <span class="accent-blue">Area</span></h2>
  <div class="map-box"><div class="map" role="img" aria-label="Map of Texas marking the service area"></div></div>
  <div class="intro">Currently, we offer services in the Texas cities of</div>
  <ul class="cities">
    <li class="current">Argyle <span>☝</span></li>
    <li>Corinth</li>
    <li>Flower Mound</li>
    <li>Lewisville</li>
  </ul>
</section>

<section class="touch">
  <h2>Get <span class="accent">In Touch</span></h2>
  <div class="field">Your Name</div>
  <div class="field">Email</div>
  <div class="field">Phone Number</div>
  <div class="radios">Preferred Contact Method
    <div class="opts"><span>Call</span><span>Text</span><span>Email</span></div>
  </div>
  <a class="btn" href="#" style="margin-top:28px;font-size:14px;padding:10px 18px">Submit <span class="arrow">➜</span></a>
</section>

<section class="contact">
  <h2>Contact <span class="accent-blue">Us</span></h2>
  <p>Contact us today at Quendle Pools &amp; Patio, and let's discuss how our professionals can help bridge the gap between what your pool could be and what it actually is! Get ready to have a worry-free experience with quality service delivered right on time so you can start enjoying those waves anytime soon!</p>
  <div class="give">Give us a call today at</div>
</section>

<footer class="footer">
  <div class="logo"><span class="mark"></span>quendle</div>
  <div class="social"><span></span><span></span><span></span><span></span></div>

  <div class="fcol" style="left:400px;width:300px">
    <h3>CONTACT US</h3>
    <div class="contact-item">
      <svg width="14" height="18" viewBox="0 0 14 18"><path d="M7 0a7 7 0 0 0-7 7c0 5 7 11 7 11s7-6 7-11a7 7 0 0 0-7-7zm0 10a3 3 0 1 1 0-6 3 3 0 0 1 0 6z" fill="#7cc521"/></svg>
      <div><small>Address</small>Mailing Address: 1450 Harbor Lane,<br>Suite 210, Frisco, TX 75034</div>
    </div>
    <div class="contact-item">
      <svg width="16" height="16" viewBox="0 0 16 16"><path d="M3 1l3 3-2 2a10 10 0 0 0 6 6l2-2 3 3-2 2C7 15 1 9 1 3z" fill="#7cc521"/></svg>
      <div><small>Call us</small>972-555-0143</div>
    </div>
    <div class="contact-item">
      <svg width="16" height="12" viewBox="0 0 16 12"><rect width="16" height="12" rx="1" fill="#7cc521"/><path d="M1 1l7 6 7-6" stroke="#0c0c0c" stroke-width="1.5" fill="none"/></svg>
      <div><small>Email</small>info@quendle-example.com</div>
    </div>
  </div>

  <div class="fcol" style="left:740px;width:200px">
    <h3>QUICK LINKS</h3>
    <ul><li>HOME</li><li>ABOUT</li><li>SERVICES</li><li>BLOG</li><li>TESTIMONIALS</li><li>CONTACT US</li></ul>
  </div>

  <div class="fcol" style="left:960px;width:200px">
    <h3>LINKS</h3>
    <ul><li>COPYRIGHT</li><li>LEGAL</li><li>PRIVACY</li><li>ACCESSIBILITY</li><li>SITEMAP</li></ul>
  </div>

  <div class="copyright">©2023, All rights reserved.</div>
  <div class="to-top"><svg width="14" height="10" viewBox="0 0 14 10"><path d="M1 9l6-7 6 7" stroke="#fff" stroke-width="2.5" fill="none"/></svg></div>
</footer>

</body>
</html>
```